BRAVO Estate Attendant

We require a website built for this company. Logo is also on the attached document. Some info on the company:<br/>To create a work class experience for our clients for property maintenance. A personalised service that deliver’s what landlords need...Quality work, on time and managed from start to finish.<br/>We do things different, our clients deal with one contact, a client manager who manages your maintenance task from start to finish. Our service allows our expert trades people to do what they do best and leave the management/organising to us!<br/>I have drafted up the layout of the web ... very brief at this stage however once we have more info we will add links and can collate more information and provide. <br/>We just want to get a layout of what you think the web should look like and can go from there.

```html
<!DOCTYPE html>
<html lang="en">
<head>
<meta charset="utf-8">
<title>BRAVO Estate Attendant</title>
<link href="https://fonts.googleapis.com/css2?family=Roboto:wght@300;400;500;700;900&display=swap" rel="stylesheet">
<style>
:root{
  --yellow:#ffc600;
  --dark:#3c3b3c;
  --darker:#353435;
  --text:#444344;
  --muted:#5a595a;
  --light:#f4f3f3;
  --white:#ffffff;
}
*{margin:0;padding:0;box-sizing:border-box}
html,body{width:1200px;height:3363px;overflow:hidden}
body{position:relative;font-family:"Roboto",sans-serif;color:var(--text);background:var(--white)}
.abs{position:absolute}
.btn{position:absolute;display:flex;align-items:center;justify-content:center;font-weight:700;text-transform:uppercase}

/* hero */
.hero{position:absolute;left:0;top:0;width:1200px;height:682px;overflow:hidden}
.hero-photo{position:absolute;left:300px;top:0;width:900px;height:682px;
  background:linear-gradient(180deg,#5f8fa8 0%,#9fc0c9 25%,#5a7f86 45%,#3d6a73 60%,#4d7a3a 78%,#3f6e2c 100%)}
.hero-shapes{position:absolute;left:0;top:0}
.logo{position:absolute;left:128px;top:22px;color:var(--dark);font-weight:400;line-height:1}
.logo .name{font-size:64px;letter-spacing:-1px;display:block}
.logo .sub{font-size:16px;letter-spacing:.3px;display:block;margin-top:2px;text-transform:uppercase}
.nav{position:absolute;top:26px;left:546px;display:flex;gap:0;height:28px}
.nav a{color:var(--white);font-weight:700;font-size:14px;text-decoration:none;display:flex;align-items:center;padding:0 7px;margin-right:14px;text-transform:uppercase}
.nav a.active{background:var(--yellow);color:var(--dark)}
.nav a svg{margin-left:6px}
.hero-title{position:absolute;left:125px;top:246px;font-size:64px;font-weight:900;color:var(--white);line-height:70px}
.hero .btn{left:133px;top:413px;width:144px;height:51px;background:var(--dark);color:var(--yellow);font-size:18px}
.slider-arrow{position:absolute;top:569px;width:33px;height:33px;border:2px solid var(--dark);display:flex;align-items:center;justify-content:center}

/* services */
.services{position:absolute;left:0;top:682px;width:1200px;height:711px;background:var(--light)}
.section-label{font-weight:700;font-size:27px;color:var(--dark);letter-spacing:.5px}
.services .section-label{position:absolute;left:128px;top:114px}
.underline{position:absolute;height:4px;width:55px;background:var(--yellow)}
.services-photo{position:absolute;left:128px;top:202px;width:312px;height:421px;
  background:linear-gradient(160deg,#6fbfe8 0%,#9ed2ee 30%,#d8dde0 55%,#8c98a2 80%,#3b4a58 100%)}
.services-photo p{position:absolute;left:23px;bottom:18px;color:var(--white);font-weight:700;font-size:17px;line-height:21px;text-transform:uppercase}
.card{position:absolute;width:189px;height:245px;background:var(--white);text-align:center;box-shadow:0 2px 6px rgba(0,0,0,.05)}
.card svg{position:absolute;left:69px;top:29px}
.card h3{position:absolute;top:106px;left:0;width:100%;font-size:15px;font-weight:500;color:var(--dark);line-height:19px}
.card p{position:absolute;top:134px;left:18px;width:153px;font-size:11px;line-height:16px;color:var(--muted)}
.card .btn{left:53px;top:200px;width:84px;height:21px;background:var(--yellow);color:var(--white);font-size:11px}
.card.tall h3{top:106px}
.card.two h3{top:102px}
.card.two p{top:143px}

/* welcome */
.welcome{position:absolute;left:0;top:1393px;width:1200px;height:644px;overflow:hidden}
.welcome-photo{position:absolute;left:420px;top:94px;width:657px;height:511px;
  background:linear-gradient(180deg,#e4e3ea 0%,#cdc8d2 35%,#9c98a8 55%,#b5b3bc 75%,#dcdde2 100%)}
.welcome-shapes{position:absolute;left:0;top:0}
.welcome-kicker{position:absolute;left:128px;top:85px;font-weight:700;font-size:17px;color:var(--dark)}
.welcome-name{position:absolute;left:120px;top:100px;font-size:150px;font-weight:300;color:var(--dark);letter-spacing:-4px;line-height:1}
.welcome-text{position:absolute;left:128px;top:348px;width:260px;font-size:16px;line-height:21px;color:var(--dark)}
.welcome .btn{left:131px;top:550px;width:105px;height:38px;background:var(--dark);color:var(--yellow);font-size:13px}
.follow{position:absolute;left:444px;top:597px;display:flex;align-items:center;gap:12px;font-weight:700;font-size:12px;color:var(--dark)}
.follow span.dot{width:28px;height:28px;border-radius:50%;border:2px solid var(--white);background:var(--yellow);display:block}

/* benefit */
.benefit-title{position:absolute;left:0;width:1200px;top:2100px;text-align:center}
.feature{position:absolute;left:128px;top:2208px;width:468px;height:444px;background:var(--light)}
.feature-photo{position:absolute;left:0;top:0;width:468px;height:262px;
  background:linear-gradient(135deg,#e9ecef 0%,#c9cfd6 40%,#a9b3be 70%,#eef0f2 100%)}
.feature h3{position:absolute;left:40px;top:293px;font-size:17px;font-weight:500;color:var(--dark)}
.feature p{position:absolute;left:40px;top:326px;width:330px;font-size:14px;line-height:20px;color:var(--muted)}
.benefit-card{position:absolute;width:221px;height:214px;background:var(--light);text-align:center}
.benefit-card svg{position:absolute;left:88px;top:32px}
.benefit-card h3{position:absolute;top:110px;width:100%;font-size:15px;font-weight:500;color:var(--dark)}
.benefit-card p{position:absolute;top:138px;left:35px;width:151px;font-size:11px;line-height:16px;color:var(--muted)}

/* cta + footer */
.cta{position:absolute;left:0;top:2729px;width:1200px;height:634px;background:var(--dark);overflow:hidden}
.cta-shapes{position:absolute;left:0;top:0}
.cta h2{position:absolute;top:70px;width:1200px;text-align:center;font-size:26px;font-weight:700;color:var(--white);text-transform:uppercase}
.cta p{position:absolute;top:122px;width:1200px;text-align:center;font-size:17px;line-height:25px;color:#e6e5e6}
.cta .btn{left:512px;top:209px;width:176px;height:52px;background:var(--yellow);color:var(--dark);font-size:17px;gap:10px}
.footer-logo{position:absolute;left:196px;top:484px;color:var(--white);font-weight:400;line-height:1}
.footer-logo .name{font-size:88px;letter-spacing:-2px;display:block}
.footer-logo .sub{font-size:21px;display:block;margin-top:2px;text-transform:uppercase}
.footer-divider{position:absolute;left:601px;top:464px;width:1px;height:150px;background:#5c5b5c}
.footer-menu{position:absolute;left:675px;top:482px;color:var(--white)}
.footer-menu h4{font-size:13px;font-weight:700}
.footer-menu nav{margin-top:18px;font-size:14px}
.footer-menu nav a{color:var(--white);text-decoration:none}
.footer-menu nav i{font-style:normal;margin:0 6px}
.footer-menu small{display:block;margin-top:40px;font-size:11px}
</style>
</head>
<body>

<header class="hero">
  <div class="hero-photo" role="img" aria-label="Photo of a blue timber house with a green lawn under an evening sky"></div>
  <svg class="hero-shapes" width="1200" height="682" viewBox="0 0 1200 682">
    <polygon points="0,0 337,0 572,346 350,682 0,682" fill="var(--yellow)"/>
    <polygon points="337,0 470,0 572,346" fill="#ffd23a" fill-opacity=".45"/>
  </svg>
  <div class="logo"><span class="name">BRAVO</span><span class="sub">Estate Attendant</span></div>
  <nav class="nav">
    <a class="active" href="#">Home</a>
    <a href="#">About Us<svg width="12" height="8" viewBox="0 0 12 8"><path d="M1 1l5 5 5-5" fill="none" stroke="#fff" stroke-width="2"/></svg></a>
    <a href="#">Services<svg width="12" height="8" viewBox="0 0 12 8"><path d="M1 1l5 5 5-5" fill="none" stroke="#fff" stroke-width="2"/></svg></a>
    <a href="#">Benefit<svg width="12" height="8" viewBox="0 0 12 8"><path d="M1 1l5 5 5-5" fill="none" stroke="#fff" stroke-width="2"/></svg></a>
    <a href="#">Contact Us</a>
  </nav>
  <h1 class="hero-title">Property<br>Concierge</h1>
  <a class="btn" href="#">Read More</a>
  <div class="slider-arrow" style="left:141px"><svg width="10" height="16" viewBox="0 0 10 16"><path d="M8 1L2 8l6 7" fill="none" stroke="#3c3b3c" stroke-width="2"/></svg></div>
  <div class="slider-arrow" style="left:189px"><svg width="10" height="16" viewBox="0 0 10 16"><path d="M2 1l6 7-6 7" fill="none" stroke="#3c3b3c" stroke-width="2"/></svg></div>
</header>

<section class="services">
  <h2 class="section-label">OUR SERVICES</h2>
  <div class="underline" style="left:128px;top:156px"></div>
  <div class="services-photo" role="img" aria-label="Photo looking up at a white curved apartment tower against a blue sky">
    <p>Lorem ipsum is simply<br>dummy text of the</p>
  </div>

  <div class="card" style="left:481px;top:118px">
    <svg width="52" height="52" viewBox="0 0 52 52" fill="none" stroke="#3c3b3c" stroke-width="2"><rect x="18" y="2" width="16" height="8" stroke="var(--yellow)"/><circle cx="14" cy="18" r="5"/><circle cx="38" cy="18" r="5"/><circle cx="26" cy="22" r="5"/><path d="M4 36c0-8 4-11 10-11s10 3 10 11M28 36c0-8 4-11 10-11s10 3 10 11"/><path d="M2 36h48M8 36v14M44 36v14"/></svg>
    <h3>Trade People</h3>
    <p>Lorem Ipsum is simply dummy text of the printing and types lorem ipsum.</p>
    <a class="btn" href="#">Read More</a>
  </div>
  <div class="card" style="left:481px;top:378px">
    <svg width="52" height="52" viewBox="0 0 52 52" fill="none" stroke="#3c3b3c" stroke-width="2"><rect x="10" y="2" width="32" height="6" rx="2"/><path d="M26 8v6"/><path d="M24 30c-6 6-4 18 2 18s8-12 2-18c0 6-4 6-4 0z"/><path d="M12 18c-3 4-3 8 0 12M40 18c3 4 3 8 0 12" stroke="var(--yellow)"/><circle cx="26" cy="20" r="2" stroke="var(--yellow)"/></svg>
    <h3>Smoke Alarms</h3>
    <p>Lorem Ipsum is simply dummy text of the printing and types lorem ipsum.</p>
    <a class="btn" href="#">Read More</a>
  </div>
  <div class="card two" style="left:688px;top:51px">
    <svg width="52" height="52" viewBox="0 0 52 52" fill="none" stroke="#3c3b3c" stroke-width="2"><path d="M4 36V26l8-10h30l6 10v10z"/><path d="M14 18h26v8H10" stroke="var(--yellow)"/><circle cx="14" cy="38" r="5"/><circle cx="40" cy="38" r="5"/><path d="M30 8h12M34 4h8"/></svg>
    <h3>Removalist van<br>and trailers</h3>
    <p>Lorem Ipsum is simply dummy text of the printing.</p>
    <a class="btn" href="#">Read More</a>
  </div>
  <div class="card" style="left:688px;top:311px">
    <svg width="52" height="52" viewBox="0 0 52 52" fill="none" stroke="#3c3b3c" stroke-width="2"><path d="M4 14h36l-6 24H2z"/><path d="M8 20h36l-6 24H6z"/><path d="M12 26h36l-6 20H10z"/><circle cx="28" cy="34" r="6" stroke="var(--yellow)"/></svg>
    <h3>Finance</h3>
    <p>Lorem Ipsum is simply dummy text of the printing and types lorem ipsum.</p>
    <a class="btn" href="#">Read More</a>
  </div>
  <div class="card" style="left:891px;top:162px">
    <svg width="52" height="52" viewBox="0 0 52 52" fill="none" stroke="#3c3b3c" stroke-width="2"><rect x="14" y="16" width="24" height="20" stroke="var(--yellow)"/><path d="M19 22h14M19 27h14M19 32h10" stroke="var(--yellow)"/><path d="M4 4h8v6M48 4h-8v6M4 48h8v-8M48 48h-8v-8M8 26h6M38 26h6"/><circle cx="4" cy="26" r="3"/><circle cx="48" cy="26" r="3"/></svg>
    <h3>Connections</h3>
    <p>Lorem Ipsum is simply dummy text of the printing and types lorem ipsum.</p>
    <a class="btn" href="#">Read More</a>
  </div>
  <div class="card" style="left:891px;top:422px">
    <svg width="52" height="52" viewBox="0 0 52 52" fill="none" stroke="#3c3b3c" stroke-width="2"><rect x="6" y="4" width="30" height="42"/><circle cx="21" cy="16" r="5" stroke="var(--yellow)"/><path d="M12 28h18M12 34h14M12 40h10"/><path d="M46 10l4 4-16 20-6 2 2-6z"/></svg>
    <h3>Wealth creation</h3>
    <p>Lorem Ipsum is simply dummy text of the printing and types lorem ipsum.</p>
    <a class="btn" href="#">Read More</a>
  </div>
</section>

<section class="welcome">
  <div class="welcome-photo" role="img" aria-label="Photo of a businessman in a suit looking out over a city skyline from a glass balcony"></div>
  <svg class="welcome-shapes" width="1200" height="644" viewBox="0 0 1200 644">
    <polygon points="0,0 709,644 0,644" fill="var(--yellow)"/>
    <polygon points="851,0 1200,0 1200,317" fill="var(--yellow)"/>
    <polygon points="851,0 1077,0 1077,206" fill="#d7a600" fill-opacity=".25"/>
  </svg>
  <p class="welcome-kicker">WELCOME TO</p>
  <h2 class="welcome-name">BRAVO</h2>
  <p class="welcome-text">Lorem ipsum dolor sit amet, consectetur adipiscing elit, sed do eiusmod tempor incididunt ut labore et dolore magna aliqua. Ut enim ad minim veniam, quis nostr ud exercitation ullamco laboris nisi ut aliquip ex ea commodo cons equat.</p>
  <a class="btn" href="#">Read More</a>
  <div class="follow">FOLLOW
    <span class="dot" aria-label="Social profile one"></span>
    <span class="dot" aria-label="Social profile two"></span>
    <span class="dot" aria-label="Social profile three"></span>
  </div>
</section>

<section>
  <h2 class="section-label benefit-title">BENEFIT</h2>
  <div class="underline" style="left:573px;top:2150px"></div>
  <div class="feature">
    <div class="feature-photo" role="img" aria-label="Photo of a smiling support agent wearing a headset in a bright open office"></div>
    <h3>Customer Service</h3>
    <p>Sed ut perspiciatis unde omnis iste natus error sit voluptatem accusantium doloremque laudantium, totam rem aperiam, eaque ipsa quae ab illo inventore</p>
  </div>
  <div class="benefit-card" style="left:610px;top:2208px">
    <svg width="46" height="52" viewBox="0 0 46 52" fill="none" stroke="#3c3b3c" stroke-width="2"><circle cx="23" cy="18" r="9"/><path d="M12 18a11 11 0 0 1 22 0M12 16v6M34 16v6M34 22c0 4-4 6-9 6" /><path d="M4 50c0-10 8-16 19-16s19 6 19 16z"/><path d="M17 36l6 8 6-8" stroke="var(--yellow)"/></svg>
    <h3>Call Centre</h3>
    <p>Lorem Ipsum is simply dummy text of the printing and types lorem ipsum.</p>
  </div>
  <div class="benefit-card" style="left:848px;top:2208px">
    <svg width="52" height="52" viewBox="0 0 52 52" fill="none" stroke="#3c3b3c" stroke-width="2"><path d="M4 18l10-10h24l10 10-22 26z"/><path d="M4 18h44M18 8l-4 10 12 26 12-26-4-10"/><path d="M46 2v6M43 5h6M6 36v6M3 39h6" stroke="var(--yellow)"/></svg>
    <h3>Values</h3>
    <p>Lorem Ipsum is simply dummy text of the printing and types lorem ipsum.</p>
  </div>
  <div class="benefit-card" style="left:610px;top:2440px">
    <svg width="52" height="52" viewBox="0 0 52 52" fill="none" stroke="#3c3b3c" stroke-width="2"><circle cx="30" cy="12" r="9" stroke="var(--yellow)"/><path d="M30 7v10" stroke="var(--yellow)"/><path d="M2 30h8v16H2zM10 32h12l10 4c4 2 2 6-2 5l-10-2M10 44l16 2 20-10c2-4-2-6-6-4l-10 4"/></svg>
    <h3>Pricing</h3>
    <p>Lorem Ipsum is simply dummy text of the printing and types lorem ipsum.</p>
  </div>
  <div class="benefit-card" style="left:848px;top:2440px">
    <svg width="48" height="52" viewBox="0 0 48 52" fill="none" stroke="#3c3b3c" stroke-width="2"><circle cx="24" cy="12" r="9"/><path d="M6 50V40c0-8 8-12 18-12s18 4 18 12v10z"/><path d="M24 28v22M18 28l6 8 6-8"/><path d="M10 42l2 4 4 1M22 44h4M34 42l2 4 2-3" stroke="var(--yellow)"/></svg>
    <h3>Level of expertise</h3>
    <p>Lorem Ipsum is simply dummy text of the printing and types lorem ipsum.</p>
  </div>
</section>

<footer class="cta">
  <svg class="cta-shapes" width="1200" height="634" viewBox="0 0 1200 634">
    <path d="M0 360 C150 420 300 440 457 422 L1200 422 L1200 634 L0 634 Z" fill="var(--darker)"/>
    <path d="M0 216 C120 330 260 400 457 422 C300 430 140 400 0 360 Z" fill="var(--yellow)"/>
  </svg>
  <h2>Lorem ipsum dolor sit amet consectetur</h2>
  <p>Sed ut perspiciatis unde omnis iste natus error sit voluptatem<br>sed do eiusmod tempor incididunt ut labore et</p>
  <a class="btn" href="#"><svg width="18" height="13" viewBox="0 0 18 13"><rect width="18" height="13" rx="1" fill="#3c3b3c"/><path d="M1 1l8 6 8-6" fill="none" stroke="#ffc600" stroke-width="1.5"/></svg>Contact Us</a>
  <div class="footer-logo"><span class="name">BRAVO</span><span class="sub">Estate Attendant</span></div>
  <div class="footer-divider"></div>
  <div class="footer-menu">
    <h4>MENU</h4>
    <nav><a href="#">Home</a><i>|</i><a href="#">About Us</a><i>|</i><a href="#">Services</a><i>|</i><a href="#">Benefits</a><i>|</i><a href="#">Contact Us</a></nav>
    <small>Copyright © 2019 All Rights Reserved</small>
  </div>
</footer>

</body>
</html>
```